ALL TYPES OF COMMERCIAL PLASTERING

TYPE OF BLOCK LETTERING WITH STAND OUT QUALITIES
WITH SOME TYPE OF LOGO
SOMETHING UNIQUE FOR THE BUILDING INDUSTRY.
QUALITY WORKMANSHIP
Updates

forgot to include my mobile phone number on my brief. could you add it to your design please MOBILE PH 0491 586 032

please let me make this quite clear ,the company name is harbourline linings and Fitouts PTY LTD. THE TYPE OF WORK WE WILL BE DOING IS COMMERCIAL PLASTERING.

Industry/Entity Type

Industry

Contact Information for Business Card

harbourline linings and fitouts P/L
marcus trelawny p.o.box 82 wendouree 3355 email address harbourlinelinings@mailcove.example
ABN 84 519 263 740 COMMERCIAL PLASTERING

```html
<!DOCTYPE html>
<html lang="en">
<head>
<meta charset="utf-8">
<title>Harbourline Linings and Fitouts – Business Card</title>
<link rel="stylesheet" href="https://fonts.googleapis.com/css2?family=Arimo:wght@400;700&display=swap">
<style>
  :root {
    --backdrop: #d8d2c8;
    --card: #050505;
    --lime: #c4dc2a;
    --white: #f4f4f4;
  }
  html, body {
    margin: 0;
    padding: 0;
    overflow: hidden;
  }
  body {
    width: 1200px;
    height: 870px;
    background: var(--backdrop);
    display: flex;
    align-items: center;
    justify-content: center;
    font-family: "Arimo", Arial, sans-serif;
  }
  .business-card {
    position: relative;
    width: 480px;
    height: 786px;
    background: var(--card);
    box-sizing: border-box;
    padding: 0 40px;
    color: var(--white);
  }
  .brand {
    position: absolute;
    top: 176px;
    left: 36px;
    right: 30px;
    display: flex;
    align-items: center;
    gap: 14px;
  }
  .brand-mark {
    flex: 0 0 auto;
    width: 70px;
    height: 70px;
  }
  .brand-name {
    margin: 0;
    color: var(--lime);
    font-weight: 700;
    font-size: 21px;
    line-height: 1.12;
    text-transform: uppercase;
    letter-spacing: 0.4px;
  }
  .brand-tagline {
    margin: 4px 0 0;
    color: var(--white);
    font-weight: 400;
    font-size: 13px;
    letter-spacing: 0.6px;
    text-transform: uppercase;
  }
  .holder-name {
    position: absolute;
    top: 382px;
    left: 40px;
    margin: 0;
    font-weight: 400;
    font-size: 34px;
    letter-spacing: 0.3px;
  }
  .contact-list {
    position: absolute;
    top: 520px;
    left: 46px;
    right: 20px;
    margin: 0;
    padding: 0;
    list-style: none;
  }
  .contact-item {
    display: flex;
    align-items: center;
    gap: 16px;
    height: 34px;
    font-size: 19px;
    letter-spacing: 0.3px;
  }
  .contact-icon {
    flex: 0 0 auto;
    width: 22px;
    height: 22px;
    fill: var(--lime);
  }
</style>
</head>
<body>
  <article class="business-card">
    <header class="brand">
      <svg class="brand-mark" viewBox="0 0 70 70" aria-hidden="true">
        <circle cx="35" cy="35" r="31" fill="none" stroke="var(--lime)" stroke-width="5"/>
      </svg>
      <div class="brand-text">
        <h1 class="brand-name">Harbourline Linings<br>and Fitouts P/L</h1>
        <p class="brand-tagline">Commercial Plastering</p>
      </div>
    </header>

    <h2 class="holder-name">marcus trelawny</h2>

    <ul class="contact-list">
      <li class="contact-item">
        <svg class="contact-icon" viewBox="0 0 24 24" aria-label="mobile">
          <path d="M7 1h10a2 2 0 0 1 2 2v18a2 2 0 0 1-2 2H7a2 2 0 0 1-2-2V3a2 2 0 0 1 2-2zm0 3v11h10V4zm2 13v2h2v-2zm4 0v2h2v-2z"/>
        </svg>
        <span>0491 586 032</span>
      </li>
      <li class="contact-item">
        <svg class="contact-icon" viewBox="0 0 24 24" aria-label="registration">
          <path d="M12 1a8 8 0 0 1 8 8c0 6-8 14-8 14S4 15 4 9a8 8 0 0 1 8-8zm0 4.5A3.5 3.5 0 1 0 12 12.5 3.5 3.5 0 0 0 12 5.5z"/>
        </svg>
        <span>ABN 84 519 263 740</span>
      </li>
      <li class="contact-item">
        <svg class="contact-icon" viewBox="0 0 24 24" aria-label="postal address">
          <path d="M12 2l11 10h-3v10h-6v-6h-4v6H4V12H1z"/>
        </svg>
        <span>p.o.box 82 wendouree 3355</span>
      </li>
      <li class="contact-item">
        <svg class="contact-icon" viewBox="0 0 24 24" aria-label="email">
          <path d="M1 5h22v14H1zm2 2v.5l9 6 9-6V7zm0 3v7h18v-7l-9 6z"/>
        </svg>
        <span>harbourlinelinings@mailcove.example</span>
      </li>
    </ul>
  </article>
</body>
</html>
```